Website Landing Page for Medical Recruitment

Looking for a landing page to add to our existing website. The objective of the page is to recruit new clinical staff for various departments within Pinecrest Medical Center (non-profit hospital in the Richmond, TX area).

We would like the page to be modern, professional, and non-cluttered. Please include call-to-actions and include a button that will navigate to the page where candidates can submit their applications (this page already exists).

Target Market(s)

25-35-year-olds who live in the Houston and Richmond area with medical experience.

Industry/Entity Type

Medical/Health

Font styles to use
Sans Serif

Colors
0054AA
0677BA
7BADD7
CADEEF
E8F1F8

Requirements
Must have
• A "call to action"; a button that navigates to pinecrestmedhub.example/careers

```html
<!DOCTYPE html>
<html lang="en">
<head>
<meta charset="utf-8">
<title>Pinecrest Medical Center – Careers</title>
<link href="https://fonts.googleapis.com/css2?family=Poppins:wght@400;500;600&family=Arimo:wght@400&display=swap" rel="stylesheet">
<style>
  :root {
    --blue-deep: #0054AA;
    --blue-mid: #0677BA;
    --blue-soft: #7BADD7;
    --blue-pale: #CADEEF;
    --blue-mist: #E8F1F8;
    --ink: #3d3d3d;
    --text: #555;
    --white: #fff;
  }
  * { box-sizing: border-box; margin: 0; padding: 0; }
  html, body { width: 1200px; height: 2435px; overflow: hidden; }
  body { position: relative; background: var(--white); font-family: "Poppins", sans-serif; color: var(--ink); }
  a { text-decoration: none; color: inherit; }

  /* Header */
  .site-header { position: absolute; top: 0; left: 0; width: 1200px; height: 114px; background: var(--white); }
  .brand { position: absolute; left: 112px; top: 32px; display: flex; align-items: center; gap: 12px; }
  .brand-dot { width: 44px; height: 44px; border-radius: 50%; background: var(--blue-mid); }
  .brand-name { font-size: 26px; font-weight: 500; color: var(--blue-mid); letter-spacing: -0.3px; }
  .header-cta { position: absolute; left: 929px; top: 12px; width: 160px; height: 50px; border-radius: 25px;
    background: var(--blue-mid); color: var(--white); font-size: 16px; font-weight: 500; display: flex; align-items: center; justify-content: center; }
  .main-nav { position: absolute; right: 112px; top: 74px; display: flex; gap: 22px; font-size: 14.5px; font-weight: 500; color: #333; }
  .main-nav .current { color: var(--blue-mid); }

  /* Hero */
  .hero { position: absolute; top: 114px; left: 0; width: 1200px; height: 709px; }
  .hero-photo { position: absolute; inset: 0;
    background: linear-gradient(180deg, #7f98b1 0%, #4d6f99 40%, #2f4f7e 75%, #2b466e 100%); }
  .hero-shade { position: absolute; inset: 0; background: rgba(10, 30, 60, 0.25); }
  .hero-content { position: absolute; left: 0; right: 0; top: 362px; text-align: center; color: var(--white); }
  .hero-title { font-size: 61px; font-weight: 600; line-height: 66px; letter-spacing: 0.5px; }
  .hero-lead { margin-top: 22px; font-size: 19px; line-height: 31px; }
  .hero-cta { display: inline-flex; align-items: center; justify-content: center; margin-top: 22px; width: 174px; height: 52px;
    border-radius: 26px; background: var(--blue-deep); font-size: 18px; font-weight: 500; letter-spacing: 0.4px; }

  /* About */
  .about-label { position: absolute; left: 112px; top: 890px; font-size: 40px; font-weight: 500; color: var(--ink); }
  .about-title { position: absolute; left: 112px; top: 940px; font-size: 28px; font-weight: 600; color: var(--blue-deep); }
  .about-copy { position: absolute; left: 112px; top: 997px; width: 463px; font-family: "Arimo", sans-serif; font-size: 14px;
    line-height: 25.8px; color: var(--text); text-align: justify; }
  .about-cta { position: absolute; left: 112px; top: 1282px; width: 141px; height: 49px; border-radius: 25px; background: var(--blue-deep);
    color: var(--white); font-size: 15px; font-weight: 500; display: flex; align-items: center; justify-content: center; }
  .about-visual { position: absolute; left: 648px; top: 900px; width: 402px; height: 402px; border-radius: 50%;
    background: radial-gradient(circle at 45% 45%, #5e9cc4 0%, #4b8cb8 60%, #3f80ad 100%); }

  /* Jobs */
  .jobs { position: absolute; top: 1402px; left: 0; width: 1200px; height: 655px; background: var(--blue-mist); }
  .jobs-title { position: absolute; top: 38px; left: 0; right: 0; text-align: center; font-size: 34px; font-weight: 600; color: var(--ink); }
  .jobs-title span { color: var(--blue-deep); }
  .jobs-rule { position: absolute; top: 89px; left: 578px; width: 44px; height: 3px; background: var(--blue-deep); }
  .jobs-lead { position: absolute; top: 103px; left: 0; right: 0; text-align: center; font-size: 16px; color: var(--text); }
  .job-card { position: absolute; top: 177px; width: 230px; height: 398px; border: 2.5px solid var(--blue-deep); border-radius: 26px;
    text-align: center; }
  .job-icon { margin: 20px auto 0; width: 127px; height: 127px; border-radius: 50%; background: var(--blue-deep);
    display: flex; align-items: center; justify-content: center; }
  .job-title { margin-top: 12px; font-size: 17px; font-weight: 500; line-height: 23px; color: var(--blue-deep); }
  .job-copy { margin: 10px auto 0; width: 200px; font-family: "Arimo", sans-serif; font-size: 14.5px; line-height: 23px; color: var(--text); }
  .job-cta { display: inline-flex; align-items: center; justify-content: center; margin-top: 19px; height: 44px; padding: 0 16px;
    border: 1.5px solid var(--blue-deep); border-radius: 22px; font-size: 14.5px; font-weight: 500; color: var(--blue-deep); }

  /* Footer */
  .site-footer { position: absolute; top: 2057px; left: 0; width: 1200px; height: 378px; background: var(--blue-deep); color: var(--white); }
  .footer-brand { position: absolute; top: 44px; left: 0; right: 0; display: flex; justify-content: center; align-items: center; gap: 16px; }
  .footer-brand .brand-dot { width: 66px; height: 66px; background: var(--white); }
  .footer-brand .brand-name { color: var(--white); font-size: 36px; }
  .footer-contact { position: absolute; top: 152px; left: 0; right: 0; text-align: center; font-size: 14.5px; font-weight: 500; letter-spacing: 0.3px; }
  .footer-contact .sep { margin: 0 20px; }
  .footer-nav { position: absolute; top: 205px; left: 0; right: 0; display: flex; justify-content: center; gap: 29px; font-size: 14.5px; font-weight: 500; }
  .social { position: absolute; top: 253px; left: 0; right: 0; display: flex; justify-content: center; gap: 7px; }
  .social a { width: 36px; height: 36px; border: 1.5px solid var(--white); border-radius: 50%; display: flex; align-items: center; justify-content: center; }
  .social a span { width: 12px; height: 12px; border-radius: 50%; background: var(--white); }
  .copyright { position: absolute; top: 313px; left: 0; right: 0; text-align: center; font-size: 15.5px; }
</style>
</head>
<body>

<header class="site-header">
  <a class="brand" href="#"><span class="brand-dot"></span><span class="brand-name">Pinecrest Medical Center</span></a>
  <a class="header-cta" href="https://pinecrestmedhub.example/careers">APPLY NOW</a>
  <nav class="main-nav">
    <a class="current" href="#">HOME</a>
    <a href="#">FIND A DOCTOR</a>
    <a href="#">ABOUT US</a>
    <a href="#">SERVICES</a>
    <a href="#">LOCATIONS</a>
    <a href="#">PATIENTS/VISITORS</a>
  </nav>
</header>

<section class="hero">
  <div class="hero-photo" role="img" aria-label="Photo of a smiling team of doctors and nurses in scrubs and white coats outside the hospital"></div>
  <div class="hero-shade"></div>
  <div class="hero-content">
    <h1 class="hero-title">PINECREST<br>MEDICAL CENTER</h1>
    <p class="hero-lead">Sed ut perspiciatis unde omnis iste natus error sit voluptatem<br>accusantium doloremque laudantium, totam</p>
    <a class="hero-cta" href="https://pinecrestmedhub.example/careers">Job Vacancies</a>
  </div>
</section>

<section class="about">
  <h2 class="about-label">ABOUT</h2>
  <h3 class="about-title">PINECREST MEDICAL CENTER</h3>
  <p class="about-copy">Sed ut perspiciatis unde omnis iste natus error sit voluptatem accusantium doloremque laudantium, totam rem aperiam, eaque ipsa quae ab illo inven tore veritatis et quasi architecto beatae vitae dicta sunt explicabo. Nemo enim ipsam voluptatem quia voluptas sit aspernatur aut odit aut fugit, sed quia consequuntur magni dolores eos qui ratione voluptatem sequi nesciunt. Neque porro quisquam est, qui dolorem ipsum quia dolor sit amet, consectetur, adipisci velit, sed quia non numquam eius modi tempora incidunt ut labore et dolore magnam aliquam quaerat voluptatem.Ut enim ad minima veniam, quis nostrum exercitationem ullam corporis suscipit laboriosam, nisi ut aliquid ex ea commodi consequatur</p>
  <a class="about-cta" href="#">READ MORE</a>
  <div class="about-visual" role="img" aria-label="Blue-tinted photo of a bright hospital lobby in a round frame"></div>
</section>

<section class="jobs">
  <h2 class="jobs-title">OUR <span>JOBS</span></h2>
  <div class="jobs-rule"></div>
  <p class="jobs-lead">Sed ut perspiciatis unde omnis iste natus error sit voluptatem accusantium</p>

  <article class="job-card" style="left:112px">
    <div class="job-icon">
      <svg width="60" height="76" viewBox="0 0 60 76" fill="none" stroke="#fff" stroke-width="2.5">
        <path d="M8 4h32l12 12v52H8z"/><path d="M40 4v12h12"/>
        <path d="M16 26h28M16 33h28M16 40h28M16 47h14"/>
        <circle cx="22" cy="58" r="7"/><path d="M17 63l-3 10 8-4 8 4-3-10"/>
      </svg>
    </div>
    <h3 class="job-title">CERTIFIED NURSES<br>ASSISTANTS</h3>
    <p class="job-copy">Sed ut perspiciatis unde omn is iste natus error sit volupta tem accusantium doloremque eaque laudantium</p>
    <a class="job-cta" href="https://pinecrestmedhub.example/careers">APPLY NOW</a>
  </article>

  <article class="job-card" style="left:361px">
    <div class="job-icon">
      <svg width="80" height="66" viewBox="0 0 80 66" fill="none" stroke="#fff" stroke-width="2.5">
        <path d="M28 64V8h26v56"/><path d="M41 14v14M34 21h14"/>
        <path d="M4 64V24h24M54 30h22v34"/><path d="M2 64h76"/>
        <path d="M12 34v26M20 34v26M36 40v24M46 40v24M62 38v22M70 38v22"/>
      </svg>
    </div>
    <h3 class="job-title">EMERGENCY ROOM<br>TECHS</h3>
    <p class="job-copy">Sed ut perspiciatis unde omn is iste natus error sit volupta tem accusantium doloremque eaque laudantium</p>
    <a class="job-cta" href="https://pinecrestmedhub.example/careers">JOB VACANCIES</a>
  </article>

  <article class="job-card" style="left:610px">
    <div class="job-icon">
      <svg width="66" height="76" viewBox="0 0 66 76" fill="none" stroke="#fff" stroke-width="2.5">
        <path d="M18 16c0-8 6-12 15-12s15 4 15 12"/><path d="M18 16h30"/>
        <path d="M20 20c0 12 5 20 13 20s13-8 13-20"/>
        <path d="M4 72c0-16 12-24 29-24s29 8 29 24z"/>
        <path d="M44 58v10M39 63h10"/>
      </svg>
    </div>
    <h3 class="job-title">LICENSED VOCATIONAL<br>NURSES</h3>
    <p class="job-copy">Sed ut perspiciatis unde omn is iste natus error sit volupta tem accusantium doloremque eaque laudantium</p>
    <a class="job-cta" href="https://pinecrestmedhub.example/careers">APPLY NOW</a>
  </article>

  <article class="job-card" style="left:858px">
    <div class="job-icon">
      <svg width="80" height="74" viewBox="0 0 80 74" fill="none" stroke="#fff" stroke-width="2.5">
        <path d="M26 4h34l12 12v54H26"/><path d="M60 4v12h12"/>
        <circle cx="50" cy="32" r="10"/><path d="M46 38V26h5a3 3 0 010 6h-5M50 32l4 6"/>
        <path d="M36 52h28M36 58h28M36 64h28"/>
        <path d="M6 48l22-22 5 5-22 22-7 2z"/>
      </svg>
    </div>
    <h3 class="job-title">REGISTERED<br>NURSES</h3>
    <p class="job-copy">Sed ut perspiciatis unde omn is iste natus error sit volupta tem accusantium doloremque eaque laudantium</p>
    <a class="job-cta" href="https://pinecrestmedhub.example/careers">JOB VACANCIES</a>
  </article>
</section>

<footer class="site-footer">
  <div class="footer-brand"><span class="brand-dot"></span><span class="brand-name">Pinecrest Medical Center</span></div>
  <p class="footer-contact">Phone : 281-555-0142<span class="sep">|</span>Email : hello@pinecrestmed.example<span class="sep">|</span>Address : 48 Alder Lane, Richmond&nbsp; Texas 77400</p>
  <nav class="footer-nav">
    <a href="#">HOME</a>
    <a href="#">FIND A DOCTOR</a>
    <a href="#">ABOUT US</a>
    <a href="#">SERVICES</a>
    <a href="#">LOCATIONS</a>
    <a href="#">PATIENTS/VISITORS</a>
  </nav>
  <div class="social">
    <a href="#" aria-label="Social link 1"><span></span></a>
    <a href="#" aria-label="Social link 2"><span></span></a>
    <a href="#" aria-label="Social link 3"><span></span></a>
    <a href="#" aria-label="Social link 4"><span></span></a>
    <a href="#" aria-label="Social link 5"><span></span></a>
  </div>
  <p class="copyright">© Copyright 2022 Pinecrest Medical Center.All Rights Reserved.</p>
</footer>

</body>
</html>
```